A multi-page brochure that explains our firm ,KVL Wealth Management

We have a current brochure attached but it is a compilation of several items combined into one. We would like this to have the same content but be one complete theme. We are a financial planning form so it needs to have a level of professionalism but also a comfortable approach for clients and showing that was have a lot of resources and experience. We cater mostly to the 55-60+ age community.

We need the front page picture changed. lake themed would be great, like our website www.TheMoskaHouse.com
Just to be clear we use KVL Wealth Management now as our company name. Parent company name is The Moska House LLC. I attached the current mock brochure and our new logos.
Our logo colors are:
KVL WM Logo Colors:

Blue:
HEX: #0f75bc
RGB: rgba(15,117,188,255)

Grey:
HEX: #6d6e71
RGB: rgba(109,110,113,255)

Target Market(s)

High-level individuals that are looking for financial guidance who are 40 years old and up

Industry/Entity Type

Wealth Management

Requirements
Must have
• Clean and crisp
Nice to have
• https://www.bramblestoneplanners.com/wealth-management-brochure , this is a sample we like

```html
<!DOCTYPE html>
<html lang="en">
<head>
<meta charset="utf-8">
<title>KVL Wealth Management – Brochure Spreads</title>
<link href="https://fonts.googleapis.com/css2?family=Montserrat:ital,wght@0,300;0,400;0,600;0,700;0,800;1,600;1,700&display=swap" rel="stylesheet">
<style>
:root{
  --blue:#0f75bc;
  --grey:#6d6e71;
  --tan:#d8ae7e;
  --ink:#1a1a1a;
  --text:#4a4a4a;
  --board:#e7e7e7;
  --black:#0b0b0b;
}
*{margin:0;padding:0;box-sizing:border-box}
html,body{width:849px;height:1200px;overflow:hidden;background:var(--board)}
body{font-family:"Montserrat",Arial,sans-serif;color:var(--ink);position:relative}
.label{position:absolute;width:154.5px;text-align:center;font-size:8.4px;font-weight:400;color:#222;letter-spacing:.2px}
.spread{position:absolute;width:309px;height:199px;background:#fff;overflow:hidden}
.tan-band{position:absolute;left:0;top:0;width:100%;height:4px;background:var(--tan)}
.foot{position:absolute;left:0;bottom:0;width:100%;height:7px;background:var(--black);color:#ddd;font-size:1.5px;display:flex;align-items:center;justify-content:space-between;padding:0 11px}
.grid-fade{position:absolute;left:0;bottom:7px;width:100%;height:14px;background:linear-gradient(180deg,#fff,#f0f0f0)}
.pg{position:absolute;top:0;width:154.5px;height:199px;overflow:hidden}
.pg.r{left:154.5px}
.abs{position:absolute}
.kicker{font-size:5px;font-weight:400;letter-spacing:.5px;text-transform:uppercase;text-align:center;color:var(--ink)}
.title{font-size:8.2px;font-weight:800;text-align:center;color:var(--ink);line-height:1}
.lede{font-size:2.3px;font-style:italic;font-weight:700;text-align:center;line-height:1.35;color:#333}
.body{font-size:2.3px;line-height:1.4;color:var(--text);text-align:justify}
.body p+p{margin-top:2.2px}
.col-head{font-size:2.9px;font-weight:700;color:#333;text-align:center;margin-bottom:1.2px;line-height:1.15}
.icon{width:4px;height:4px;border-radius:50%;background:var(--tan);margin:0 auto 1.2px}
.list{list-style:none;font-size:2.2px;line-height:1.45;color:var(--text);margin-top:1.5px}
.list li::before{content:"• ";color:var(--tan)}
.photo{position:absolute}
.cover-back{position:absolute;inset:0;background:var(--black);color:#fff;text-align:center}
.cover-back .intro{font-size:3px;letter-spacing:.3px;text-transform:uppercase;margin-top:46px;line-height:1.3;color:#fff}
.cover-back .big{font-size:5.6px;font-weight:800;line-height:1.1;margin-top:1px}
.cover-back h4{font-size:3px;font-weight:700;margin-top:5px}
.cover-back .txt{font-size:2.3px;line-height:1.35;padding:0 24px;margin-top:1.5px;color:#e4e4e4}
.brand{font-weight:600;white-space:nowrap;line-height:1}
.cover-back .brand{font-size:8.6px;color:#fff;margin-top:19px}
.cover-back .addr{font-size:2.2px;line-height:1.4;margin-top:10px;color:#ddd}
.cover-back .disc{font-size:1.8px;line-height:1.35;margin-top:3px;color:#bbb;padding:0 30px}
.front-title{font-size:7.4px;font-weight:700;color:var(--blue);text-align:center}
.front-sub{font-size:3.7px;color:var(--grey);text-align:center;margin-top:1.5px}
.front-brand{font-size:8.6px;color:var(--blue);text-align:center}
.caption{position:absolute;bottom:0;left:0;width:100%;background:rgba(0,0,0,.75);color:#fff;font-size:2px;text-align:center;padding:1px 0}
.blackbox{background:#111;color:#fff;font-size:2.3px;font-style:italic;font-weight:700;line-height:1.35;padding:3px 4px}
.person-name{font-size:3.2px;font-weight:700;color:#333}
.person-role{font-size:1.8px;color:#888;margin:.5px 0 1px}
.note{font-size:1.7px;line-height:1.35;color:#777}
</style>
</head>
<body>

<div class="label" style="left:101px;top:15px">Back Cover</div>
<div class="label" style="left:255.5px;top:15px">Front Cover</div>
<div class="label" style="left:439px;top:15px">Page 1</div>
<div class="label" style="left:593.5px;top:15px">Page 2</div>

<section class="spread" style="left:101px;top:29px">
  <div class="pg">
    <div class="cover-back">
      <div class="intro">A Personalized<br>Wealth Management Plan</div>
      <div class="big">can open up<br>a future of possibilities.</div>
      <h4>Our Professional Guidance</h4>
      <div class="txt">Although life is complex, we hope you take reassurance from knowing that you have a partner in planning. As you've seen, many variables must be coordinated to maximize the benefits of your financial plan. We're eager to work together on your next steps, so we can create the most effective plan to manage your wealth and fulfill your vision.</div>
      <h4>Results for the Long Haul</h4>
      <div class="txt">Wealth management is more than just assessing where you need to go, developing a strategy to get there, and executing that strategy; it's also about monitoring your progress over the long term. We recognize that as your life evolves, your financial needs will also change. Together, we'll anticipate significant life events and incorporate them into your strategy. When unplanned events happen, we'll evaluate them together to determine the right course of action.</div>
      <div class="brand">KVL Wealth Management</div>
      <div class="addr">18 Alder Ridge Parkway, Suite 210 | Lakewood Falls, MN 55490<br>440 Harbor Point Drive, Suite 500 | Bayview Shores, CA 94099<br>555.014.2286 | 800.555.0199<br>www.TheMoskaHouse.com</div>
      <div class="disc">Securities and advisory services offered through Harborline Financial Network, Member Clearwater Investor Council, a Registered Investment Adviser. Fixed insurance products and services are separate from and not offered through Harborline Financial Network.</div>
    </div>
  </div>
  <div class="pg r">
    <div class="photo" role="img" aria-label="Calm mountain lake with clear water and rocky shore" style="left:0;top:0;width:154.5px;height:128px;background:linear-gradient(180deg,#eef3f5 0%,#c9d6dc 30%,#7f9c94 50%,#5f8e8a 62%,#a7b59a 80%,#8a7c62 100%)"></div>
    <div class="abs" style="left:0;top:139px;width:100%">
      <div class="front-title">Wealth Management</div>
      <div class="front-sub">Focused on Your Needs and Vision</div>
    </div>
    <div class="abs front-brand brand" style="left:0;top:165px;width:100%">KVL Wealth Management</div>
  </div>
</section>

<section class="spread" style="left:439px;top:29px">
  <div class="tan-band"></div>
  <div class="pg">
    <div class="abs" style="left:0;top:21px;width:100%"><div class="kicker">Partner With</div><div class="title">a Specialist</div></div>
    <div class="abs body" style="left:45px;top:43px;width:64px">
      <p>Understanding your unique needs and vision for the future is the starting point for our relationship. Together, we'll assess where you are financially and where you want to be. Next, we'll create a comprehensive wealth management plan that addresses your immediate and long-term goals. What about the unpredictable? We'll plan for the changes that may be ahead, too.</p>
      <p>Exploring the topics of interest presented in this brochure will give you an idea of the depth and breadth of our services. Rest assured that we'll partner with you throughout the planning process, always circling back to this fundamental question: what's right for you and your loved ones?</p>
    </div>
    <div class="photo" role="img" aria-label="Two advisors reviewing a plan on a laptop" style="left:45px;top:107px;width:64px;height:42px;background:linear-gradient(135deg,#2f4a66,#9fb2c2 55%,#e5e8ea)"></div>
  </div>
  <div class="pg r">
    <div class="abs" style="left:0;top:21px;width:100%"><div class="kicker">Our</div><div class="title">Firm</div></div>
    <div class="abs body" style="left:8px;top:43px;width:68px">
      <p>The Moska House LLC, established in 1987, is an independent, full-service, financial consulting firm.</p>
      <p>As we search the marketplace for innovative, strategic solutions, The Moska House is guided by the following principles:</p>
      <p>• <b>SERVICE</b> – We seek to anticipate your needs and exceed your expectations in every aspect of our partnership.</p>
      <p>• <b>PLANNING</b> – We collaborate with you by listening, asking questions, educating and helping you make informed decisions so skillfully implement appropriate, effective financial strategies.</p>
      <p>• <b>INTEGRITY</b> – We build long-term client relationships and are proud of the integrity and sensitivity we exhibit when working with all our clients.</p>
      <p>The Moska House has created an environment of objectivity and independence in which to provide independent guidance and access to the widest variety of fiscal tools to support your financial goals. Our work complements the services of your existing advisors, including accountants and attorneys.*</p>
      <p>The degree and sophistication of the plan varies according to your circumstances.</p>
      <p class="note">*The Moska House LLC does not provide specific tax or legal advice. Please consult your accountant and/or attorney.</p>
    </div>
    <div class="photo" role="img" aria-label="Brick office building with glass entrance" style="left:81px;top:43px;width:63px;height:50px;background:linear-gradient(180deg,#8fb6d9,#c9dbe9 45%,#8a4a36 60%,#6d8a4a 100%)"><div class="caption">Lakewood Falls Location</div></div>
    <div class="photo" role="img" aria-label="Modern glass office tower against blue sky" style="left:81px;top:100px;width:63px;height:50px;background:linear-gradient(160deg,#1e5fa8,#5fa0dc 45%,#d7e7f5 70%,#2a6fb8)"><div class="caption">Bayview Shores Location</div></div>
  </div>
  <div class="grid-fade"></div>
  <div class="foot"><span>Securities and advisory services offered through Harborline Financial Network, Member Clearwater Investor Council,</span><span>a Registered Investment Adviser. Fixed insurance products and services offered through Northgate Insurance Agency or The Moska House.</span></div>
</section>

<div class="label" style="left:101px;top:251px">Page 3</div>
<div class="label" style="left:255.5px;top:251px">Page 4</div>
<div class="label" style="left:439px;top:251px">Page 5</div>
<div class="label" style="left:593.5px;top:251px">Page 6</div>

<section class="spread" style="left:101px;top:265px">
  <div class="tan-band"></div>
  <div class="pg">
    <div class="abs" style="left:0;top:27px;width:100%"><div class="kicker">Our</div><div class="title">Philosophy</div></div>
    <div class="abs body" style="left:46px;top:51px;width:64px">
      <p>Our philosophy is based on empowering our clients through education. After taking the time to understand your goals, needs and challenges, we help you to understand and organize all aspects of your finances and create a plan of action.</p>
      <p>The framework used to develop your plan is the 6-step <b><i>Wealth Management Process</i></b>, a flexible system that allows us to effectively customize a plan suited to your unique circumstances. During each step of the process, we take the time to provide a detailed explanation of our recommendations and why they are best suited for your situation.</p>
      <p>After all your questions have been answered, and you are confident in your decisions, we begin to implement a course of action. By actively learning and participating in the planning process, you retain control each step of the way. Once your investment program is implemented, we will monitor the performance of your investments and consult with you regularly to help ensure that the program continues to reflect your goals and objectives.</p>
      <p>The Moska House strives to develop a relationship in which you will feel more knowledgeable, informed and empowered as a result of working with us.</p>
    </div>
  </div>
  <div class="pg r">
    <div class="photo" role="img" aria-label="Older couple sitting on a lakeside dock at sunset" style="left:0;top:4px;width:154.5px;height:188px;background:linear-gradient(180deg,#f2efe9 0%,#d9dedd 30%,#b9bcb3 48%,#8fa3a8 62%,#6d7f80 80%,#9a8c74 100%)"></div>
  </div>
  <div class="foot"><span>Securities and advisory services offered through Harborline Financial Network, Member Clearwater Investor Council,</span><span>a Registered Investment Adviser. Fixed insurance products and services offered through Northgate Insurance Agency or The Moska House.</span></div>
</section>

<section class="spread" style="left:439px;top:265px">
  <div class="tan-band"></div>
  <div class="pg">
    <div class="photo" role="img" aria-label="Audience attending a seminar in a bright room" style="left:0;top:4px;width:154.5px;height:188px;background:linear-gradient(180deg,#f5f5f3 0%,#d8d6d0 35%,#6f6f70 60%,#3a3a3c 80%,#c9c6c0 100%)"></div>
  </div>
  <div class="pg r">
    <div class="abs" style="left:0;top:36px;width:100%"><div class="kicker">Working With</div><div class="title">A Certified Planner</div></div>
    <div class="abs lede" style="left:10px;top:58px;width:134px">When selecting a financial planner, you need to feel confident that the person you choose to help you plan for your future is competent and ethical. Many people believe that all financial planners are certified, but this isn't true. Only those who have fulfilled the certification and renewal requirements of the Planner Standards Board can use the certification marks.</div>
    <div class="abs" style="left:8px;top:79px;width:64px">
      <div style="font-size:2.8px;font-weight:700;color:#333;margin-bottom:3px">Certification Requirements</div>
      <div class="body">
        <p>• <b>EDUCATION:</b> Certified planners must develop their theoretical and practical financial planning knowledge by completing a comprehensive course of study at a college or university offering a financial planning curriculum approved by the standards board.</p>
        <p>• <b>EXAMINATION:</b> Certified practitioners must pass a comprehensive, two-day, 10-hour certification examination that tests their ability to apply financial planning knowledge in an integrated format. Based on regular research of what planners do, the exam covers the financial planning process, tax planning, employee benefits and retirement planning, estate planning, investment management, and insurance.</p>
      </div>
    </div>
    <div class="abs" style="left:80px;top:79px;width:1px;height:60px;background:#ccc"></div>
    <div class="abs body" style="left:84px;top:79px;width:62px">
      <p>• <b>EXPERIENCE:</b> Certified professionals must have a minimum of three years' experience in the financial planning process prior to earning the right to use the certification. As a result, practitioners possess financial counseling skills in addition to financial planning knowledge.</p>
      <p>• <b>ETHICS:</b> As a final step to certification, practitioners agree to abide by a strict code of professional conduct, known as the board's Code of Ethics and Professional Responsibility, which sets forth their ethical responsibilities to the public, clients, and employers. The board also performs a background check during this process, and each candidate must disclose any investigations or legal proceedings related to his or her professional or business conduct.</p>
    </div>
  </div>
  <div class="grid-fade" style="left:154.5px;width:154.5px"></div>
  <div class="foot"><span>Securities and advisory services offered through Harborline Financial Network, Member Clearwater Investor Council,</span><span>a Registered Investment Adviser. Fixed insurance products and services offered through Northgate Insurance Agency or The Moska House.</span></div>
</section>

<div class="label" style="left:101px;top:487px">Page 7</div>
<div class="label" style="left:255.5px;top:487px">Page 8</div>
<div class="label" style="left:439px;top:487px">Page 9</div>
<div class="label" style="left:593.5px;top:487px">Page 10</div>

<section class="spread" style="left:101px;top:501px">
  <div class="tan-band"></div>
  <div class="pg">
    <div class="abs" style="left:0;top:16px;width:100%"><div class="kicker">Where Do</div><div class="title">We Add Value?</div></div>
    <div class="abs blackbox" style="left:11px;top:38px;width:68px;height:37px">With so many professionals, corporations, and even websites offering investment advice, it's easy to get confused by the array of services, products, and plans. Prospective clients often ask us, "Where do you add value? What distinguishes you from the pack?" What follows is a brief response designed to assure you that partnering with our firm could be among the wisest decisions you ever make.</div>
    <div class="photo" role="img" aria-label="Calculator resting on printed financial statements" style="left:79px;top:38px;width:65px;height:37px;background:linear-gradient(135deg,#e9e9e9,#a9a9a9 50%,#d6d6d6)"></div>
    <div class="abs body" style="left:11px;top:81px;width:63px">
      <p>There are literally hundreds of thousands of people in the field of financial services who are as investment advisors, managing a client's portfolio for a fee or earning commissions on trades. But few of them ever consider doing anything beyond investments. We believe that we can offer superior investment guidance while providing something more comprehensive wealth management.</p>
      <p>Our approach to planning is carefully designed for our clients. Our planning services are as unique and diverse as the clients we serve. Because there is no cookie-cutter solution when it comes to managing our clients' financial futures, we stock our shelves with the finest financial ingredients and cook up customized solutions that leave our clients calling for seconds. The cooking analogy aside, we partner with our clients to help make their goals a reality, preserving their wealth, preparing for tomorrow, and putting it all together.</p>
    </div>
    <div class="abs body" style="left:80px;top:81px;width:64px">
      <p>As stated above, accumulation of assets is just one of several areas that we focus on. We also provide expertise in retirement planning, estate planning, risk management, taxation, business planning, and asset allocation. This commitment to a life planning approach makes financial planning personal and addresses specific individual needs. We employ a dynamic educational process that allows clients to visualize their personal goals and model the financial consequences of their choices. We rely on state-of-the-art software to plan and illustrate our strategies. We have partnerships with accountants, attorneys, and other professionals dedicated to working as a team to meet all aspects of our clients' needs. Most important, what separates our firm from the others are the relationships we develop with our clients. We built our firm based on the fundamental elements of mutual trust, honesty, and respect, which helps us better strive to help make your goals a reality.</p>
    </div>
  </div>
  <div class="pg r">
    <div class="photo" role="img" aria-label="Friends sharing an outdoor dinner under string lights" style="left:0;top:39px;width:146px;height:111px;background:linear-gradient(160deg,#f3e6c8 0%,#c9b189 30%,#7a6a52 55%,#b98c74 75%,#e7d6c2 100%)"></div>
  </div>
  <div class="grid-fade"></div>
  <div class="foot"><span>Securities and advisory services offered through Harborline Financial Network, Member Clearwater Investor Council,</span><span>a Registered Investment Adviser. Fixed insurance products and services offered through Northgate Insurance Agency or The Moska House.</span></div>
</section>

<section class="spread" style="left:439px;top:501px">
  <div class="tan-band"></div>
  <div class="pg">
    <div class="abs" style="left:0;top:11px;width:100%"><div class="kicker">Wealth</div><div class="title">Accumulation</div></div>
    <div class="abs lede" style="left:16px;top:25px;width:122px">Wealth accumulation planning addresses your investment needs, focusing on the effective allocation of your assets according to your goals and risk tolerance.</div>
    <div class="abs" style="left:16px;top:34px;width:38px">
      <div class="icon"></div><div class="col-head">Asset Allocation</div>
      <div class="body">Asset allocation is the process of distributing your investments across a variety of asset categories. Our goal is to create a balance of potential risk and return that meets your goals and is comfortable for you. We'll develop integrated strategies that address:</div>
      <ul class="list"><li>Portfolio optimization</li><li>Risk analysis</li><li>Tax planning</li><li>Your investment policy statement</li></ul>
    </div>
    <div class="abs" style="left:58px;top:34px;width:38px">
      <div class="icon"></div><div class="col-head">Basic Needs</div>
      <div class="body">To plan wisely, we'll focus on your basic financial needs and create a plan to fulfill your lifestyle desires—what you seek to accomplish with your assets. We'll discuss and evaluate your needs for:</div>
      <ul class="list"><li>Cash flow</li><li>Education funds</li><li>Eldercare planning</li><li>Emergency funds</li><li>Homes and mortgages</li><li>Insurance protection</li><li>Retirement savings</li><li>Savings and investments</li></ul>
    </div>
    <div class="abs" style="left:100px;top:34px;width:38px">
      <div class="icon"></div><div class="col-head">Alternative Investments</div>
      <div class="body">Alternative investments have historically reacted differently to market volatility than traditional investments. This ability to provide diversification* is one reason we may consider including some of the following in your portfolio:</div>
      <ul class="list"><li>Commodities</li><li>Hedge funds</li><li>Infrastructure</li><li>Oil and gas</li><li>Private credit</li><li>Private equity</li><li>Real estate</li></ul>
    </div>
    <div class="abs" style="left:16px;top:106px;width:38px">
      <div class="icon"></div><div class="col-head">Solutions for<br>Special Situations</div>
      <div class="body">Your financial position may require specialized planning to help you take advantage of the following:</div>
      <ul class="list"><li>Stock options</li><li>Concentrated equity positions</li><li>Employee benefits</li><li>Employee stock ownership plans (ESOPs)</li><li>Margin strategies</li><li>Option income strategies</li><li>Restricted stock sales</li><li>1031 exchanges</li></ul>
    </div>
    <div class="abs" style="left:58px;top:110px;width:38px">
      <div class="icon"></div><div class="col-head">Basic Securities</div>
      <div class="body">A key step in accumulation planning is to choose the right mix of investments, which may include the following vehicles:</div>
      <ul class="list"><li>Risk analysis</li><li>Portfolio optimization</li><li>Tax planning</li><li>Your investment policy statement</li></ul>
    </div>
    <div class="abs" style="left:100px;top:110px;width:38px">
      <div class="icon"></div><div class="col-head">Basic Securities:<br>Traditional Investments</div>
      <div class="body">Another key step in accumulation planning is to choose the right mix of basic securities, which include:</div>
      <ul class="list"><li>Stocks</li><li>Bonds</li><li>Mutual funds</li><li>Exchange-traded funds</li><li>Short-term assets</li><li>Stock options</li><li>Annuities</li></ul>
    </div>
  </div>
  <div class="pg r">
    <div class="photo" role="img" aria-label="Sailboat deck and mast on calm open water" style="left:8px;top:15px;width:131px;height:109px;background:linear-gradient(180deg,#f4f6f8 0%,#dfe5ea 40%,#b7c3cd 60%,#7d8e9b 80%,#c9ced2 100%)"></div>
    <div class="abs note" style="left:8px;top:126px;width:131px;text-align:justify">*Diversification and asset allocation do not assure a profit or protect against a loss during a market decline. Investments are subject to risk, including the loss of principal. Some investments are not suitable for all investors, and there is no guarantee that any investing goal will be met. Alternative investments involve special risks, such as risk associated with leveraging the investment, utilizing complex financial derivatives, adverse market forces, regulatory and tax code changes, and illiquidity. Investors can lose all or a substantial amount of their investment. Past performance is no guarantee of future results. Talk to your financial advisor before making any investing decision.</div>
  </div>
  <div class="grid-fade"></div>
  <div class="foot"><span>Securities and advisory services offered through Harborline Financial Network, Member Clearwater Investor Council,</span><span>a Registered Investment Adviser. Fixed insurance products and services offered through Northgate Insurance Agency or The Moska House.</span></div>
</section>

<div class="label" style="left:101px;top:723px">Page 11</div>
<div class="label" style="left:255.5px;top:723px">Page 12</div>
<div class="label" style="left:439px;top:723px">Page 13</div>
<div class="label" style="left:593.5px;top:723px">Page 14</div>

<section class="spread" style="left:101px;top:737px">
  <div class="tan-band"></div>
  <div class="pg">
    <div class="abs" style="left:0;top:14px;width:100%"><div class="kicker" style="font-size:4.4px">Harborline's Investment</div><div class="title" style="font-size:7px">Management and Research Team</div></div>
    <div class="abs lede" style="left:11px;top:32px;width:134px">Harborline's Investment Management and Research consultants work with us to help ensure that you receive prudent investment advice. Team members apply their expertise to asset allocation recommendations and advanced portfolio construction while delivering timely insight on market opportunities and investment performance—all so you can be confident you've selected the products and strategies to best satisfy your goals. Learn more about the team below.</div>
    <div class="photo" role="img" aria-label="Portrait of investment team member" style="left:11px;top:55px;width:40px;height:35px;background:linear-gradient(180deg,#f0f0f0,#c9c9c9)"></div>
    <div class="abs" style="left:56px;top:55px;width:89px"><div class="person-name">Grant Holloway</div><div class="person-role">Managing Principal, Chief Investment Officer</div><div class="body" style="font-size:1.8px">As managing principal, he oversees the firm's investment research and portfolio management teams, serving as a trusted voice on markets, the economy and long-term investing. He holds a bachelor's degree and an MBA, and is a regular speaker for client events and industry conferences across the country.</div></div>
    <div class="photo" role="img" aria-label="Portrait of investment team member" style="left:11px;top:96px;width:40px;height:35px;background:linear-gradient(180deg,#f0f0f0,#c9c9c9)"></div>
    <div class="abs" style="left:56px;top:96px;width:89px"><div class="person-name">Owen Decker</div><div class="person-role">Managing Principal, Co-Chief Investment Officer</div><div class="body" style="font-size:1.8px">As co-chief investment officer, he is responsible for oversight of the investment management and research team, including manager due diligence, asset allocation and the firm's model portfolios. He holds a bachelor's degree in finance and several industry registrations.</div></div>
    <div class="photo" role="img" aria-label="Portrait of investment team member" style="left:11px;top:137px;width:40px;height:35px;background:linear-gradient(180deg,#f0f0f0,#c9c9c9)"></div>
    <div class="abs" style="left:56px;top:137px;width:89px"><div class="person-name">Miles Renner</div><div class="person-role">Senior Vice President, Alternative Investments</div><div class="body" style="font-size:1.8px">As senior vice president, he is responsible for analysis, approval and ongoing monitoring of all alternative investment products, including private equity, private credit, hedge funds, real assets and infrastructure. He graduated from college and holds several industry designations.</div></div>
  </div>
  <div class="pg r">
    <div class="photo" role="img" aria-label="Portrait of investment team member" style="left:6px;top:37px;width:40px;height:35px;background:linear-gradient(180deg,#f0f0f0,#c9c9c9)"></div>
    <div class="abs" style="left:51px;top:37px;width:92px"><div class="person-name">Neil Ashford</div><div class="person-role">Vice President, Equity Research</div><div class="body" style="font-size:1.8px">He oversees the asset management team and is responsible for due diligence and portfolio management of the firm's preferred portfolio services models. He also manages the firm's select equity portfolios, including income, sustainable, all-cap and disciplined growth strategies.</div></div>
    <div class="photo" role="img" aria-label="Portrait of investment team member" style="left:6px;top:85px;width:40px;height:35px;background:linear-gradient(180deg,#f0f0f0,#c9c9c9)"></div>
    <div class="abs" style="left:51px;top:85px;width:92px"><div class="person-name">Evan Castellano</div><div class="person-role">Director, Investment Management and Research</div><div class="body" style="font-size:1.8px">He joined the firm as a member of the retirement team and later joined the investment research team. He is responsible for advisor inquiries related to portfolio construction, asset allocation and manager selection. He holds a bachelor's degree and several industry registrations.</div></div>
    <div class="photo" role="img" aria-label="Portrait of investment team member" style="left:6px;top:135px;width:40px;height:35px;background:linear-gradient(180deg,#f0f0f0,#c9c9c9)"></div>
    <div class="abs" style="left:51px;top:135px;width:92px"><div class="person-name">Luke Brandt</div><div class="person-role">Director, Alternative Investments</div><div class="body" style="font-size:1.8px">As director of alternative investments, he facilitates due diligence and research activities on products within alternative financial strategies, including managed futures, hedge funds, private credit, private equity and structured products.</div></div>
  </div>
  <div class="grid-fade"></div>
  <div class="foot"><span>Securities and advisory services offered through Harborline Financial Network, Member Clearwater Investor Council,</span><span>a Registered Investment Adviser. Fixed insurance products and services offered through Northgate Insurance Agency or The Moska House.</span></div>
</section>

<section class="spread" style="left:439px;top:737px">
  <div class="tan-band"></div>
  <div class="pg">
    <div class="photo" role="img" aria-label="Portrait of investment team member" style="left:11px;top:11px;width:40px;height:36px;background:linear-gradient(180deg,#f0f0f0,#c9c9c9)"></div>
    <div class="abs" style="left:56px;top:11px;width:89px"><div class="person-name">Paul Whitacre</div><div class="person-role">Chief Market Strategist</div><div class="body" style="font-size:1.8px">As chief market strategist, he represents the firm in media appearances, advisor speaking events and commentary on markets, providing timely context on economic conditions, equity and fixed income markets, and the outlook for client portfolios across market cycles.</div></div>
    <div class="photo" role="img" aria-label="Portrait of investment team member" style="left:11px;top:53px;width:40px;height:36px;background:linear-gradient(180deg,#f0f0f0,#c9c9c9)"></div>
    <div class="abs" style="left:56px;top:53px;width:89px"><div class="person-name">Dean Hollis</div><div class="person-role">Director, Fixed Income</div><div class="body" style="font-size:1.8px">With more than a decade of investment research experience, he focuses on fixed income markets and strategy, managing the firm's bond portfolios, evaluating interest rate risk, credit trends and monetary policy to help guide advisors and their clients toward balanced decisions.</div></div>
    <div class="photo" role="img" aria-label="Portrait of investment team member" style="left:11px;top:96px;width:40px;height:36px;background:linear-gradient(180deg,#f0f0f0,#c9c9c9)"></div>
    <div class="abs" style="left:56px;top:96px;width:89px"><div class="person-name">Corey Halvorsen</div><div class="person-role">Manager, Investment Due Diligence</div><div class="body" style="font-size:1.8px">As manager, he helps lead the firm's model portfolio program and the due diligence process for mutual funds, exchange-traded funds, asset allocation and tactical strategies. He holds several industry registrations and a graduate degree in economics and finance.</div></div>
    <div class="photo" role="img" aria-label="Portrait of investment team member" style="left:11px;top:139px;width:40px;height:36px;background:linear-gradient(180deg,#f0f0f0,#c9c9c9)"></div>
    <div class="abs" style="left:56px;top:139px;width:89px"><div class="person-name">Scott Pemberton</div><div class="person-role">Supervisor, Investment Management and Research Consulting</div><div class="body" style="font-size:1.8px">He joined the firm as a consultant and now leads the research consulting team, providing comprehensive solutions to investment-related questions, portfolio reviews and advisory platform guidance to advisors across the network.</div></div>
  </div>
  <div class="pg r">
    <div class="abs" style="left:0;top:22px;width:100%"><div class="kicker">Estate</div><div class="title">Planning</div></div>
    <div class="abs lede" style="left:10px;top:40px;width:134px">An estate plan is a master plan to protect your property during your life and distribute it according to your wishes after your death. A comprehensive estate plan sets personalized goals for protecting your assets and preserving your wealth. We help guide the estate planning process and collaborate with your legal advisor to ensure your plan is properly structured and reflects your personal goals.</div>
    <div class="abs" style="left:10px;top:58px;width:42px">
      <div class="icon"></div><div class="col-head">Asset Protection</div>
      <div class="body">Where do you want your assets to go eventually? Who should handle the management of your estate or business? By looking ahead, we'll help uncover special issues that may include providing for your family's financial security and protecting your assets against future threats. A thorough plan to protect your assets should evaluate:</div>
      <ul class="list"><li>Business ownership issues</li><li>Liability insurance</li><li>Trusts—domestic, offshore, other</li><li>Special needs trusts</li></ul>
    </div>
    <div class="abs" style="left:56px;top:58px;width:42px">
      <div class="icon"></div><div class="col-head">Charitable Giving</div>
      <div class="body">Most people donate to charities because they believe in the charity's mission and contributing gives them a sense of personal satisfaction. At the same time, charitable giving can help minimize your income and estate taxes. To meet your personal goals and tax-incentive needs, we may discuss:</div>
      <ul class="list"><li>Donor-advised funds</li><li>Income and estate deductions</li><li>Charitable trusts</li><li>Private foundations</li></ul>
    </div>
    <div class="abs" style="left:102px;top:58px;width:42px">
      <div class="icon"></div><div class="col-head">Transfer of Wealth</div>
      <div class="body">It's wise to plan early for the future distribution of your assets, including your estate or business. We'll discuss strategies to enable the smooth transfer of your wealth, according to your wishes, as well as the management of your assets during your disability or incapacity. Important topics include:</div>
      <ul class="list"><li>Business succession</li><li>Children from a previous marriage</li><li>Equalizing inheritances</li><li>Estate probate management</li><li>Lifetime giving</li></ul>
    </div>
    <div class="photo" role="img" aria-label="Aerial view of a green coastline and sea" style="left:84px;top:140px;width:70.5px;height:39px;background:linear-gradient(135deg,#9fc0c8,#6f9a6a 45%,#c9c39a 70%,#eef1ee)"></div>
  </div>
  <div class="grid-fade" style="left:154.5px;width:154.5px"></div>
  <div class="foot"><span>Securities and advisory services offered through Harborline Financial Network, Member Clearwater Investor Council,</span><span>a Registered Investment Adviser. Fixed insurance products and services offered through Northgate Insurance Agency or The Moska House.</span></div>
</section>

<div class="label" style="left:101px;top:959px">Page 15</div>
<div class="label" style="left:255.5px;top:959px">Page 16</div>
<div class="label" style="left:439px;top:959px">Page 17</div>
<div class="label" style="left:593.5px;top:959px">Page 18</div>

<section class="spread" style="left:101px;top:974px">
  <div class="tan-band"></div>
  <div class="pg">
    <div class="abs" style="left:0;top:18px;width:100%"><div class="kicker">Risk</div><div class="title">Management</div></div>
    <div class="abs lede" style="left:22px;top:36px;width:110px">Risks and losses related to liability, business ownership, property loss, and illness or disability are part of everyday life. Risk management identifies your sources of risk and customizes strategies to minimize them.</div>
    <div class="abs" style="left:16px;top:50px;width:38px">
      <div class="icon"></div><div class="col-head">Asset Protection</div>
      <div class="body">How can you protect yourself from risks such as lawsuits, accidents, and property damage? Asset protection planning seeks to transfer these risks through protections available under the law, such as:</div>
      <ul class="list"><li>Personal liability analysis</li><li>Professional liability analysis</li><li>Property and casualty insurance</li><li>Umbrella coverage</li><li>Ownership and beneficiary designations</li><li>Legal covenants</li></ul>
    </div>
    <div class="abs" style="left:58px;top:50px;width:38px">
      <div class="icon"></div><div class="col-head">Business Concerns</div>
      <div class="body">As a business owner, you have many options for managing your risk exposure. We'll address the impact of your type of business, the states you do business in, and other essential factors. Your options for handling these risks may include:</div>
      <ul class="list"><li>Liability insurance</li><li>Property and casualty insurance</li><li>Workers' compensation</li><li>Business interruption insurance</li><li>Advisory board</li><li>Employee retention</li><li>Financial controls</li><li>Legal documents</li></ul>
    </div>
    <div class="abs" style="left:100px;top:50px;width:38px">
      <div class="icon"></div><div class="col-head">Life and Health Insurance</div>
      <div class="body">Genetics and lifestyle affect your risk profile for life and health insurance. Maintaining a healthy lifestyle and obtaining recommended medical care can reduce your insurance premiums. Factors such as being overweight, smoking, and driving unsafely can increase your premiums. To ensure that you have comprehensive coverage, it's wise to consider:</div>
      <ul class="list"><li>Health insurance</li><li>Life insurance</li><li>Disability insurance</li><li>Group insurance benefits</li><li>Long-term care insurance</li></ul>
    </div>
  </div>
  <div class="pg r">
    <div class="abs" style="left:0;top:18px;width:100%"><div class="kicker">Business</div><div class="title">Planning</div></div>
    <div class="abs lede" style="left:22px;top:36px;width:110px">If you're a business owner and shareholder, your business is likely your most significant asset. With proper planning and risk management, you should be able to tap the value of your business to support your retirement or transfer your business's value to your family in the event of your death.</div>
    <div class="abs" style="left:14px;top:54px;width:58px">
      <div class="icon"></div><div class="col-head">Executive Compensation</div>
      <div class="body">As an executive, you may be entitled to both cash and non-cash compensation, depending on the size and structure of your company. Common examples of executive compensation include:</div>
      <ul class="list"><li>Health insurance benefits</li><li>Stock options</li><li>Nonqualified deferred compensation</li><li>Personal performance incentives</li><li>Qualified retirement plans</li><li>Cafeteria plan compensation</li></ul>
    </div>
    <div class="abs" style="left:14px;top:128px;width:58px">
      <div class="icon"></div><div class="col-head">Operations Planning</div>
      <div class="body">Of the many variables that affect the performance of a business over its life cycle, only some are in your control. Two factors that can be controlled through careful wealth management are:</div>
      <ul class="list"><li>Asset management</li><li>Tax issues</li></ul>
    </div>
    <div class="abs" style="left:82px;top:54px;width:58px">
      <div class="icon"></div><div class="col-head">Risk Management</div>
      <div class="body">Running a business carries identifiable risks to the safety of your personal and business assets. We'll consider business-specific options for handling these risks through:</div>
      <ul class="list"><li>Liability insurance</li><li>Property and casualty insurance</li><li>Business interruption insurance</li></ul>
    </div>
    <div class="abs" style="left:82px;top:117px;width:58px">
      <div class="icon"></div><div class="col-head">Succession Planning</div>
      <div class="body">Do you have a detailed plan for the transition of your business to a new owner? When life changes suddenly, you'll be better positioned to adapt if you understand:</div>
      <ul class="list"><li>Buy-sell agreements</li><li>ESOPs</li><li>Positioning your business for sale</li><li>The valuation of your business</li></ul>
    </div>
  </div>
  <div class="grid-fade"></div>
  <div class="foot"><span>Securities and advisory services offered through Harborline Financial Network, Member Clearwater Investor Council,</span><span>a Registered Investment Adviser. Fixed insurance products and services offered through Northgate Insurance Agency or The Moska House.</span></div>
</section>

<section class="spread" style="left:439px;top:974px">
  <div class="tan-band"></div>
  <div class="pg">
    <div class="abs" style="left:0;top:13px;width:100%"><div class="kicker">Tax</div><div class="title">Planning</div></div>
    <div class="abs lede" style="left:14px;top:31px;width:126px">Effective tax planning considers the implications of individual, investment, and business decisions, with a view to minimizing tax liability. Although wealth planning decisions are rarely made solely on their tax impact, it's wise to consider the tax issues and costs involved.</div>
    <div class="abs" style="left:12px;top:45px;width:40px">
      <div class="icon"></div><div class="col-head">Business Tax Planning</div>
      <div class="body">Tax issues are never far from a business owner's mind, and many of your decisions will likely be tax based. Consider the following factors:</div>
      <ul class="list"><li>Business entity choices</li><li>Income, losses, and deductions</li><li>State tax planning</li><li>Benefit planning</li></ul>
    </div>
    <div class="abs" style="left:12px;top:104px;width:40px">
      <div class="icon"></div><div class="col-head">Investment Tax Planning</div>
      <div class="body">We'll evaluate how to position your assets to minimize your annual taxes. This requires year-round planning, and it helps to understand:</div>
      <ul class="list"><li>Gains and losses</li><li>Mutual fund taxation</li><li>Qualified dividends</li><li>Tax-deferred investments</li><li>Tax-exempt investments</li><li>1031 exchanges</li><li>Wash sales</li></ul>
    </div>
    <div class="abs" style="left:57px;top:45px;width:40px">
      <div class="icon"></div><div class="col-head">Gift and Estate Tax Planning</div>
      <div class="body">If you give away wealth, during life or at death, you may incur federal gift taxes, estate taxes, and, in some cases, additional state taxes. We'll help protect the assets you transfer with strategies that aim to minimize:</div>
      <ul class="list"><li>Federal death taxes</li><li>Generation-skipping transfer tax</li><li>State death taxes</li><li>Taxation of trusts</li></ul>
    </div>
    <div class="abs" style="left:57px;top:106px;width:40px">
      <div class="icon"></div><div class="col-head">Life Event Planning</div>
      <div class="body">The significant events in your life come with tax considerations. Your wealth management plan will evaluate the tax implications of:</div>
      <ul class="list"><li>Education expenses</li><li>Marriage or divorce</li><li>Retirement</li><li>Inherited wealth</li><li>Terminal illness</li><li>Death in the family</li></ul>
    </div>
    <div class="abs" style="left:102px;top:45px;width:40px">
      <div class="icon"></div><div class="col-head">Income Tax Planning</div>
      <div class="body">Minimizing federal income tax liability can often be achieved by reducing taxable income through income deferral or shifting. Your income tax burden can also change due to:</div>
      <ul class="list"><li>Timing of deductions</li><li>Alternative minimum tax</li><li>Charitable deductions</li><li>Estimated tax payments</li><li>Kiddie tax</li><li>Social security benefits</li></ul>
    </div>
    <div class="abs note" style="left:102px;top:132px;width:40px;text-align:center">Harborline Financial Network does not provide legal or tax advice. You should consult a legal or tax professional regarding your individual situation.</div>
  </div>
  <div class="pg r">
    <div class="abs" style="left:0;top:13px;width:100%"><div class="kicker">Retirement</div><div class="title">Planning</div></div>
    <div class="abs lede" style="left:14px;top:31px;width:126px">Your retirement years may span decades, so it's wise to start planning early. A successful retirement plan should quickly dominate other financial goals during your earning and wealth-building years.</div>
    <div class="abs" style="left:10px;top:44px;width:42px">
      <div class="icon"></div><div class="col-head">Distribution Methods</div>
      <div class="body">One key to any successful retirement plan is a distribution strategy. Your plan should provide for stable monthly payments during retirement, as well as early access to your assets if needed. Our strategic discussion will consider:</div>
      <ul class="list"><li>Cash flow analysis</li><li>Beneficiary planning</li><li>Qualified plans</li><li>Nonqualified plans</li></ul>
    </div>
    <div class="abs" style="left:10px;top:110px;width:42px">
      <div class="icon"></div><div class="col-head">Executive Compensation</div>
      <div class="body">As a business owner or executive, you may have access to other tax-advantaged retirement savings vehicles, including:</div>
      <ul class="list"><li>Executive bonus</li><li>401(k) mirror plans</li><li>Corporate-owned life insurance</li><li>Nonqualified deferred compensation plans</li><li>Split dollar life insurance</li><li>Supplemental life insurance</li></ul>
    </div>
    <div class="abs" style="left:56px;top:44px;width:42px">
      <div class="icon"></div><div class="col-head">Employer-Sponsored Plans</div>
      <div class="body">Contributions to employer-sponsored pension and retirement plans are taken out of your paycheck before taxes, and your investments grow tax deferred. An employer match may be one reason to maximize your contribution. Popular options include:</div>
      <ul class="list"><li>401(k) plans</li><li>Defined benefit pension plans</li><li>403(b) and 457 plans</li><li>Profit-sharing plans</li><li>Cash balance plans</li><li>ESOPs</li></ul>
    </div>
    <div class="abs" style="left:102px;top:44px;width:42px">
      <div class="icon"></div><div class="col-head">Personal Savings</div>
      <div class="body">It's essential to identify the gap between what you'll need in retirement and what you have already saved. Once we evaluate that number, we'll develop a personalized savings strategy that will consider:</div>
      <ul class="list"><li>Basic needs</li><li>Basic securities</li><li>Asset allocation</li><li>Death in the family</li><li>Alternative investments</li><li>Government pensions</li><li>Real property</li></ul>
    </div>
    <div class="abs" style="left:102px;top:113px;width:42px">
      <div class="icon"></div><div class="col-head">Individual Retirement Accounts (IRAs)</div>
      <div class="body">IRAs are easy to establish and maintain and offer favorable tax incentives. Many people consolidate retirement savings with:</div>
      <ul class="list"><li>Traditional IRAs</li><li>Roth IRAs</li><li>Rollover IRAs</li><li>SEP IRAs</li><li>SIMPLE IRAs</li><li>Spousal IRAs</li></ul>
    </div>
  </div>
  <div class="grid-fade"></div>
  <div class="foot"><span>Securities and advisory services offered through Harborline Financial Network, Member Clearwater Investor Council,</span><span>a Registered Investment Adviser. Fixed insurance products and services offered through Northgate Insurance Agency or The Moska House.</span></div>
</section>

</body>
</html>
```